Climbing Gear Company Stationary Design

We need some new stationary to standardise our business.
We require:

Business Card
A4 Letterhead
With complements slip

Our business is a Distributor and retailer of rock climbing equipment throughout Australia.
We need to the stationary (business card in particular) to reflect this.

Target Market(s)

customers, other retail outlets, overseas manufacturers.

Industry/Entity Type

Business

Requirements
Must have
• company logo
website url- www.ridgetopgearworks.com.au
email - mark@ridgetopgearworks.com
Business Address: Unit 3, 14-16 Marlowe Street, Tallowood Bay, QLD, 2371
Phone: 0438 627 194
my Name (on Business card) - Gordon Pellimore
use of Blue colour in our logo

```html
<!DOCTYPE html>
<html lang="en">
<head>
<meta charset="utf-8">
<title>Ridgetop Gearworks – Business Card</title>
<link rel="stylesheet" href="https://fonts.googleapis.com/css2?family=Source+Sans+3:wght@400;600;700&display=swap">
<style>
  :root {
    --brand-blue: #2a4a8e;
    --ink: #4a4a4a;
    --card-face: #f4f5f6;
    --card-edge: #e6e7e9;
    --backdrop: #e9e6e1;
  }
  * { box-sizing: border-box; margin: 0; padding: 0; }
  html, body {
    width: 1200px; height: 483px; overflow: hidden;
    background: var(--backdrop);
    font-family: "Source Sans 3", sans-serif;
  }
  .stage { position: relative; width: 1200px; height: 483px; }
  .card {
    position: absolute; top: 85px; width: 524px; height: 298px;
    border-radius: 14px; overflow: hidden;
    background: linear-gradient(180deg, #fbfbfc 0%, var(--card-face) 60%, var(--card-edge) 100%);
    box-shadow: 0 3px 8px rgba(0,0,0,0.25);
  }
  .card--front { left: 55px; }
  .card--back { left: 619px; }

  .wordmark {
    position: absolute; color: var(--brand-blue);
    font-weight: 700; text-transform: uppercase; white-space: nowrap; line-height: 1;
  }
  .tagline {
    position: absolute; color: var(--brand-blue);
    font-weight: 400; text-transform: uppercase; white-space: nowrap; line-height: 1;
  }
  .rule { position: absolute; left: 0; right: 0; height: 2px; background: var(--brand-blue); }
  .rule-bar { position: absolute; right: 0; height: 8px; background: var(--brand-blue); }

  .card--front .wordmark { left: 35px; top: 68px; font-size: 25px; letter-spacing: 0.5px; }
  .card--front .tagline { left: 36px; top: 99px; font-size: 10.5px; letter-spacing: 2.5px; }
  .card--front .rule { top: 133px; }
  .card--front .rule-bar { top: 132px; width: 219px; }

  .holder-name {
    position: absolute; left: 61px; top: 222px;
    color: var(--brand-blue); font-weight: 700; font-size: 14.5px;
    text-transform: uppercase; letter-spacing: 0.2px;
  }
  .contact {
    position: absolute; left: 305px; top: 178px;
    color: var(--ink); font-size: 11.5px; line-height: 16.5px;
  }
  .contact .address { margin-bottom: 10px; }
  .contact .url-domain { font-size: 12.5px; }

  .card--back .wordmark { left: 38px; top: 52px; font-size: 35px; letter-spacing: 0.8px; }
  .card--back .tagline { left: 38px; top: 95px; font-size: 14px; letter-spacing: 4.2px; }
  .card--back .rule { top: 159px; }
  .card--back .rule-bar { top: 160px; width: 105px; }
  .card--back .site {
    position: absolute; left: 110px; top: 228px;
    color: var(--brand-blue); font-size: 13px; letter-spacing: 2.2px;
  }
</style>
</head>
<body>
<main class="stage">
  <section class="card card--front" aria-label="Business card front">
    <p class="wordmark">Ridgetop Gearworks</p>
    <p class="tagline">The Kit•The Climb•The Way of Life</p>
    <div class="rule"></div>
    <div class="rule-bar"></div>
    <p class="holder-name">Gordon Pellimore</p>
    <div class="contact">
      <p class="address">Unit 3, 14-16 Marlowe Street<br>Tallowood Bay, QLD, 2371</p>
      <p>P : 0438 627 194</p>
      <p>E : mark@ridgetopgearworks.com</p>
      <p>W: www.<span class="url-domain">ridgetopgearworks</span>.com.au</p>
    </div>
  </section>

  <section class="card card--back" aria-label="Business card back">
    <p class="wordmark">Ridgetop Gearworks</p>
    <p class="tagline">The Kit•The Climb•The Way of Life</p>
    <div class="rule"></div>
    <div class="rule-bar"></div>
    <p class="site">www.ridgetopgearworks.com.au</p>
  </section>
</main>
</body>
</html>
```